Lume wine label

Get all the info (Picture of another bottle & Logo) on a label on a thin wrap label, label size 1.5" width and 11-12" length. Also need Wine Name "LUME" and grape varietal "Gamay" and "Alc. By Vol. 12.8%"

```html
<!DOCTYPE html>
<html lang="en">
<head>
<meta charset="utf-8">
<title>Lume wine label</title>
<link rel="stylesheet" href="https://fonts.googleapis.com/css2?family=Cinzel:wght@400&display=swap">
<style>
  :root {
    --page: #efece6;
    --label-dark: #1f1f1f;
    --label-mid: #3a3a3a;
    --gold: #d39a1e;
    --frame-gold: #b8871f;
    --ink-light: #f4f4f4;
  }
  html, body {
    margin: 0;
    padding: 0;
    width: 1200px;
    height: 331px;
    overflow: hidden;
    background: var(--page);
  }
  .canvas {
    position: relative;
    width: 1200px;
    height: 331px;
  }
  .wrap-label {
    position: absolute;
    left: 20px;
    top: 94px;
    width: 1160px;
    height: 142px;
    overflow: hidden;
  }
  .damask-field {
    position: absolute;
    inset: 0;
    background: radial-gradient(ellipse at 50% 40%, var(--label-mid) 0%, #2b2b2b 45%, var(--label-dark) 100%);
  }
  .gold-frame {
    position: absolute;
    left: 10px;
    top: 10px;
    right: 10px;
    bottom: 10px;
    border: 1px solid var(--frame-gold);
  }
  .panel {
    position: absolute;
    top: 0;
    width: 560px;
    height: 142px;
  }
  .panel--first { left: 0; }
  .panel--second { left: 586px; }
  .brand {
    position: absolute;
    left: 40px;
    top: 42px;
    display: flex;
    align-items: center;
    gap: 10px;
  }
  .wine-name {
    margin: 0;
    font-family: "Cinzel", serif;
    font-weight: 400;
    font-size: 72px;
    line-height: 1;
    color: var(--gold);
  }
  .brand-mark {
    width: 26px;
    height: 26px;
    border-radius: 50%;
    background: var(--gold);
  }
  .wine-details {
    position: absolute;
    left: 288px;
    top: 46px;
    margin: 0;
    font-family: "Cinzel", serif;
    font-weight: 400;
    font-size: 30px;
    line-height: 30px;
    color: var(--ink-light);
    white-space: nowrap;
  }
  .wine-details span { display: block; }
</style>
</head>
<body>
  <div class="canvas">
    <div class="wrap-label">
      <div class="damask-field" role="img" aria-label="Dark charcoal damask pattern background"></div>
      <div class="gold-frame"></div>

      <div class="panel panel--first">
        <div class="brand">
          <p class="wine-name">LUME</p>
          <div class="brand-mark" role="img" aria-label="Place for the grape cluster emblem"></div>
        </div>
        <p class="wine-details">
          <span class="varietal">GAMAY</span>
          <span class="abv">Alc. By Vol. 12.8%</span>
        </p>
      </div>

      <div class="panel panel--second">
        <div class="brand">
          <p class="wine-name">LUME</p>
          <div class="brand-mark" role="img" aria-label="Place for the grape cluster emblem"></div>
        </div>
        <p class="wine-details">
          <span class="varietal">GAMAY</span>
          <span class="abv">Alc. By Vol. 12.8%</span>
        </p>
      </div>
    </div>
  </div>
</body>
</html>
```